Travel Agency Website - Simple General

Need a 7 page simple design that is pretty repetitive. Need to be able to load quickly that is SEO optimized. Trying to give ideas on what they can do, be personal as we are local, but at the same time come across as professional and get information easily with little burden.

- Landing Page
- Brimwell Vacations Page
- Family Trips
- Road Trips from Texas
- Other Destinations
- About Us Page
- Contact Us Page

Target Market(s)

Families

Coding

Coded - Design and coding required

Number of Pages Required

5+ page

Colors

Designer to choose colors to be used in the design.

Requirements
Must have
• Like it to flow easily with our logo. Use that for colors, etc.

```html
<!DOCTYPE html>
<html lang="en">
<head>
<meta charset="utf-8">
<title>Wandering Lark Travel Co.</title>
<link href="https://fonts.googleapis.com/css2?family=Encode+Sans+Semi+Condensed:wght@500;600&family=Figtree:wght@400;500;600;700&family=Kaushan+Script&display=swap" rel="stylesheet">
<style>
:root{
  --teal:#3a8585;
  --deep:#175a6c;
  --ink:#1f3a44;
  --gold:#c79a4e;
  --sky:#b9d9e8;
  --mist:#eef5f9;
  --body:#2b3a40;
  --muted:#4d5d63;
  --bar:#1f5264;
  --arrow:#2c8cc4;
}
*{box-sizing:border-box;margin:0;padding:0}
html,body{width:1200px;height:2821px;overflow:hidden}
body{position:relative;font-family:"Figtree",sans-serif;color:var(--body);background:var(--mist)}
.abs{position:absolute}
.hero{left:0;top:0;width:1200px;height:660px;background:linear-gradient(180deg,#a9d4e6 0%,#cfe6f0 45%,#eef5f9 80%)}
.brand-mark{left:84px;top:24px;width:116px;height:92px;display:flex;align-items:center;justify-content:center;gap:6px;font-family:"Encode Sans Semi Condensed",sans-serif;font-weight:600;font-size:17px;color:var(--deep);text-align:center;line-height:1.05}
.brand-mark .dot{width:10px;height:10px;border-radius:50%;background:var(--gold);flex:none}
.nav{left:289px;top:62px;display:flex;gap:13px;font-size:12px;font-weight:700;color:var(--deep);letter-spacing:.1px;white-space:nowrap}
.contact-btn{left:998px;top:57px;width:128px;height:34px;border-radius:17px;background:#fff;display:flex;align-items:center;justify-content:center;gap:6px;font-size:12px;font-weight:700;color:var(--deep)}
.hero-name{left:0;top:132px;width:1200px;text-align:center;font-family:"Encode Sans Semi Condensed",sans-serif;font-weight:600;font-size:52px;color:var(--deep);line-height:1.05}
.hero-name small{display:block;font-size:18px;letter-spacing:3px;color:var(--gold);font-weight:600}
.tagline{left:0;top:288px;width:1200px;text-align:center;font-family:"Encode Sans Semi Condensed",sans-serif;font-weight:500;font-size:38px;line-height:48px;color:var(--deep)}
.cta{top:400px;height:43px;border-radius:22px;color:#fff;font-weight:700;font-size:14.5px;display:flex;align-items:center;justify-content:center;white-space:nowrap}
.cta.primary{left:404px;width:206px;background:var(--teal)}
.cta.secondary{left:617px;width:180px;background:var(--gold)}
.features{left:60px;top:514px;width:1080px;display:flex;justify-content:space-around}
.feature{width:170px;text-align:center;font-size:13.5px;font-weight:600;color:var(--deep);line-height:18px}
.feature .ico{display:block;margin:0 auto 8px;width:48px;height:48px;border-radius:12px}
.card-img{border-radius:10px}
.card-title{font-family:"Encode Sans Semi Condensed",sans-serif;font-weight:500;font-size:19px;color:var(--deep)}
.card-sub{font-size:12.5px;color:var(--muted)}
.arrow{width:18px;height:14px}
.personal{left:0;top:1692px;width:1200px;height:436px;background:linear-gradient(180deg,#b9d7ea 0%,#d6e8f3 60%,#e9f2f8 100%)}
.script-head{left:100px;top:1770px;font-family:"Kaushan Script",cursive;font-size:40px;color:var(--deep);white-space:nowrap}
.lead{left:100px;top:1838px;width:560px;font-size:20px;font-weight:700;color:#111;line-height:25px}
.mission{left:100px;top:1918px;width:560px;font-size:20px;line-height:24px;color:#111}
.personal-img{left:699px;top:1780px;width:420px;height:286px;border-radius:8px;background:linear-gradient(180deg,#7fa9d4 0%,#b8cde0 55%,#c8a89a 80%,#7d7a78 100%)}
.explore-head{left:0;top:2176px;width:1200px;text-align:center;font-family:"Encode Sans Semi Condensed",sans-serif;font-weight:500;font-size:38px;color:var(--deep)}
.pills{left:10px;width:1180px;display:flex;justify-content:center;gap:12px}
.pill{flex:none;white-space:nowrap;height:43px;padding:0 19px;border:1.5px solid var(--teal);border-radius:22px;display:flex;align-items:center;font-size:14.5px;color:var(--muted);background:transparent}
.pill.active{background:var(--teal);color:#fff}
.footer{left:0;top:2497px;width:1200px;height:277px;background:#fff}
.footer-mark{left:104px;top:2560px;width:192px;height:150px;display:flex;align-items:center;justify-content:center;gap:8px;font-family:"Encode Sans Semi Condensed",sans-serif;font-weight:600;font-size:24px;color:var(--deep);text-align:center;line-height:1.1}
.footer-mark .dot{width:14px;height:14px;border-radius:50%;background:var(--gold);flex:none}
.fcol h4{font-size:13px;font-weight:600;color:var(--ink);letter-spacing:.3px;margin-bottom:8px;white-space:nowrap}
.fcol a{display:block;font-size:12px;color:var(--muted);text-decoration:none;line-height:25px;white-space:nowrap}
.fcontact{left:837px;top:2574px;font-size:15px;color:var(--ink);white-space:nowrap}
.fcontact .row{display:flex;align-items:center;gap:10px;height:34px}
.social{left:870px;top:2645px;display:flex;gap:6px}
.social span{width:32px;height:32px;border-radius:5px;display:block}
.bottom-bar{left:0;top:2774px;width:1200px;height:47px;background:var(--bar);color:#e6eef1;font-size:12px;display:flex;align-items:center;justify-content:center}
</style>
</head>
<body>

<section class="abs hero" aria-label="Hero"></section>
<div class="abs brand-mark"><span class="dot"></span>Wandering Lark<br>Travel Co.</div>
<nav class="abs nav">
  <span>HOME</span><span>BRIMWELL VACATIONS</span><span>FAMILY TRIPS</span><span>ROAD TRIPS FROM TEXAS</span><span>OTHER DESTINATIONS</span><span>ABOUT US</span>
</nav>
<div class="abs contact-btn">
  <svg width="17" height="15" viewBox="0 0 17 15" fill="none" stroke="#175a6c" stroke-width="1.4"><rect x="1" y="1" width="10" height="7" rx="1.5"/><path d="M3 8v3l3-3"/><rect x="7" y="5" width="9" height="6" rx="1.5"/></svg>
  CONTACT US
</div>

<h1 class="abs hero-name">Wandering Lark<small>TRAVEL CO.</small></h1>
<p class="abs tagline">Creating unforgettable journeys for families,<br>dreamers, and adventure seekers.</p>
<a class="abs cta primary">Start Planning Your Trip</a>
<a class="abs cta secondary">Explore Destinations</a>

<div class="abs features">
  <div class="feature"><span class="ico" role="img" aria-label="Calendar with plane icon" style="background:#3c79c4"></span>Personalized Vacation<br>Planning</div>
  <div class="feature"><span class="ico" role="img" aria-label="Globe with suitcase icon" style="background:#4a8fbf;border-radius:50%"></span>Brimwell Vacation<br>Experts</div>
  <div class="feature"><span class="ico" role="img" aria-label="Mountain road icon" style="background:#b59462"></span>Texas Road Trip<br>Adventures</div>
  <div class="feature"><span class="ico" role="img" aria-label="World globe icon" style="background:#4d9ad0;border-radius:50%"></span>Destinations<br>Worldwide</div>
  <div class="feature"><span class="ico" role="img" aria-label="Family and landmark tower icon" style="background:#d0706a"></span>Family-Focused<br>Experiences</div>
</div>

<div class="abs card-img" role="img" aria-label="Coastal bay with mountains and turquoise sea" style="left:31px;top:714px;width:553px;height:362px;background:linear-gradient(180deg,#5aa2e0 0%,#8a8a6a 35%,#2f9bb5 65%,#5d8a3c 100%)"></div>
<div class="abs card-title" style="left:31px;top:1093px">Brimwell Vacations – Land and Sea</div>
<div class="abs card-sub" style="left:31px;top:1118px">Where Magic Meets Adventure</div>
<svg class="abs arrow" style="left:557px;top:1097px" viewBox="0 0 18 14" fill="none" stroke="#2c8cc4" stroke-width="2"><path d="M1 7h15M10 1l6 6-6 6"/></svg>

<div class="abs card-img" role="img" aria-label="Family cheering toward snowy mountains at sunset" style="left:616px;top:714px;width:553px;height:362px;background:linear-gradient(180deg,#5d79b0 0%,#b9b4b8 38%,#9a7350 65%,#4a3628 100%)"></div>
<div class="abs card-title" style="left:616px;top:1093px">Family Trips</div>
<div class="abs card-sub" style="left:616px;top:1118px">Together is the Best Destination</div>
<svg class="abs arrow" style="left:1149px;top:1097px" viewBox="0 0 18 14" fill="none" stroke="#2c8cc4" stroke-width="2"><path d="M1 7h15M10 1l6 6-6 6"/></svg>

<div class="abs card-img" role="img" aria-label="Truck driving through a stone tunnel in desert canyon" style="left:31px;top:1167px;width:553px;height:363px;background:linear-gradient(180deg,#9a7a62 0%,#b5a08a 45%,#7a6558 70%,#4b4440 100%)"></div>
<div class="abs card-title" style="left:31px;top:1547px">Texas Road Trips</div>
<div class="abs card-sub" style="left:31px;top:1572px">Adventure Starts on the Open Road</div>
<svg class="abs arrow" style="left:557px;top:1551px" viewBox="0 0 18 14" fill="none" stroke="#2c8cc4" stroke-width="2"><path d="M1 7h15M10 1l6 6-6 6"/></svg>

<div class="abs card-img" role="img" aria-label="Family exploring a world globe together at home" style="left:616px;top:1167px;width:553px;height:363px;background:linear-gradient(135deg,#8f9596 0%,#d3b07a 35%,#e6e2de 60%,#b86b6e 100%)"></div>
<div class="abs card-title" style="left:616px;top:1547px">Other Destinations</div>
<div class="abs card-sub" style="left:616px;top:1572px">Discover beaches, cities, cruises, and dream destinations worldwide.</div>
<svg class="abs arrow" style="left:1149px;top:1551px" viewBox="0 0 18 14" fill="none" stroke="#2c8cc4" stroke-width="2"><path d="M1 7h15M10 1l6 6-6 6"/></svg>

<section class="abs personal" aria-label="About our planning"></section>
<h2 class="abs script-head">Travel Planning Made Personal</h2>
<p class="abs lead">Helping travelers create meaningful memories with customized experiences.</p>
<p class="abs mission">At Wandering Lark Travel Co., we believe travel should be exciting, easy, and unforgettable. Our mission is to help families and travelers discover the perfect vacation with personalized planning, expert guidance, and stress-free service from start to finish.</p>
<div class="abs personal-img" role="img" aria-label="Fairytale castle at a theme park with visitors"></div>

<h2 class="abs explore-head">Explore more on Wandering Lark</h2>
<div class="abs pills" style="top:2260px">
  <span class="pill">Brimwellland California</span><span class="pill">Brimwell Cruise Line Caribbean</span><span class="pill active">Yellowstone National Park</span><span class="pill">Smoky Mountains Family Retreat</span><span class="pill">Destin, Florida</span>
</div>
<div class="abs pills" style="top:2318px">
  <span class="pill">Hawaii Island Adventure</span><span class="pill">Alaska Cruise Journey</span><span class="pill">Texas Hill Country Adventure</span><span class="pill">Paris &amp; Rome Vacation</span><span class="pill">Brimwellland Paris</span>
</div>
<div class="abs pills" style="top:2380px">
  <span class="pill">Gatlinburg &amp; Pigeon Forge, Tennessee</span><span class="pill">Big Bend National Park</span><span class="pill">Waco Weekend Getaway</span><span class="pill">Kailani Brimwell Resort Hawaii</span>
</div>

<footer class="abs footer"></footer>
<div class="abs footer-mark"><span class="dot"></span>Wandering Lark<br>Travel Co.</div>
<div class="abs fcol" style="left:404px;top:2580px">
  <h4>QUICK LINK</h4><a>HOME</a><a>ABOUT US</a><a>CONTACT US</a>
</div>
<div class="abs fcol" style="left:579px;top:2578px">
  <h4>TRAVEL VACATIONS</h4><a>BRIMWELL VACATIONS</a><a>FAMILY TRIPS</a><a>ROAD TRIPS FROM TEXAS</a><a>OTHER DESTINATIONS</a>
</div>
<div class="abs fcontact">
  <div class="row"><svg width="22" height="22" viewBox="0 0 24 24" fill="#3a8585"><path d="M6.6 10.8a15 15 0 006.6 6.6l2.2-2.2c.3-.3.7-.4 1-.2 1.1.4 2.3.6 3.6.6.6 0 1 .4 1 1V20c0 .6-.4 1-1 1A17 17 0 013 4c0-.6.4-1 1-1h3.5c.6 0 1 .4 1 1 0 1.3.2 2.5.6 3.6.1.3 0 .7-.2 1z"/></svg>Phone: (555) 014-2387</div>
  <div class="row"><svg width="24" height="18" viewBox="0 0 24 18" fill="#3a8585"><path d="M0 0h24v18H0z" opacity=".95"/><path d="M1 1l11 8 11-8" stroke="#fff" stroke-width="1.6" fill="none"/></svg><span style="text-decoration:underline">hello@wanderinglarktravel.com</span></div>
</div>
<div class="abs social">
  <span style="background:#3b5b9a"></span><span style="background:#c1358a"></span>
</div>
<div class="abs bottom-bar">© Wandering Lark Travel Co. 2026 – All Rights Reserved</div>

</body>
</html>
```